Academic and Business book cover

I need a book cover for my academic and business book.
The focus is in international / global negotiation and influence (how to negotiate across cultures).
The book will be published on Zelvorn, both in Vaspet and printed edition. therefore I need something that works under Zelvorn guidelines.The final design should be elegant and still be able to stand out against the competition.
I would like to have orange+grey for the text colors on the cover, even if different options are welcome.
Title and my name are in the attached word doc.

Target Market(s)

graduates, Phds, from international business schools. Managers

Industry/Entity Type

Business

Font styles to use
Serif
Sans Serif

Colors

Designer to choose colors to be used in the design.

Requirements
Must have
• The title and my name should have elegant fonts.
Nice to have
• pictures of the world that don't have the "usual" Europe in the centre.

```html
<!DOCTYPE html>
<html lang="en">
<head>
<meta charset="utf-8">
<title>The Bridge Method – Book Cover</title>
<link rel="stylesheet" href="https://fonts.googleapis.com/css2?family=Arimo:wght@400;700&display=swap">
<style>
  :root {
    --page: #ffffff;
    --cover: #1b1b21;
    --spine-edge: #2c2c33;
    --orange: #f5a533;
    --light: #e6e6e8;
    --white: #ffffff;
    --tab-grey: #5a5a5f;
  }
  * { margin: 0; padding: 0; box-sizing: border-box; }
  html, body { width: 1200px; height: 1000px; overflow: hidden; background: var(--page); }
  body { position: relative; font-family: "Arimo", Arial, sans-serif; }

  .jacket {
    position: absolute; left: 100px; top: 144px; width: 990px; height: 744px;
    background: var(--cover);
    box-shadow: 4px 6px 10px rgba(0,0,0,0.35);
  }

  /* Back cover */
  .back { position: absolute; left: 0; top: 0; width: 465px; height: 744px; }
  .back-rule { position: absolute; left: 34px; top: 76px; width: 397px; height: 3px; background: var(--orange); }
  .blurb, .bio {
    position: absolute; left: 34px; width: 397px;
    color: var(--white); font-size: 9.6px; font-weight: 700; line-height: 18px;
    text-align: justify;
  }
  .blurb { top: 91px; }
  .bio { top: 303px; }
  .bio .author-name { color: var(--orange); }

  /* Spine */
  .spine {
    position: absolute; left: 465px; top: 0; width: 60px; height: 744px;
    border-left: 1px solid var(--spine-edge); border-right: 1px solid var(--spine-edge);
  }
  .spine svg { position: absolute; left: 0; top: 0; }

  /* Front cover */
  .front { position: absolute; left: 525px; top: 0; width: 465px; height: 744px; overflow: hidden; }
  .tab { position: absolute; top: 76px; width: 45px; height: 45px; background: var(--tab-grey); }
  .tab-left { left: 0; }
  .tab-right { right: 0; }
  .title {
    position: absolute; left: 0; width: 465px; top: 77px; text-align: center;
    color: var(--orange); font-size: 34px; font-weight: 700;
  }
  .subtitle {
    position: absolute; left: 0; width: 465px; top: 135px; text-align: center;
    color: var(--light); font-size: 24px; font-weight: 700; line-height: 36px;
  }
  .emblem-area {
    position: absolute; left: 80px; top: 234px; width: 305px; height: 424px;
    background: linear-gradient(180deg, #3f8a3c 0%, #d8821e 35%, #e7c21c 55%, #1c5a92 80%, #3f8a3c 100%);
  }
  .author {
    position: absolute; left: 0; width: 465px; top: 684px; text-align: center;
    color: var(--orange); font-size: 26px; font-weight: 700;
  }
</style>
</head>
<body>
  <div class="jacket">
    <section class="back">
      <div class="back-rule"></div>
      <div class="blurb">
        <p>Western notions of negotiation and influence are coming under question: old familiar concepts, such as power, <em>interests</em>, and above all, <em>BATNA</em>, take on different meanings in an international context.</p>
        <p>Adopting an interdisciplinary approach and staying away from academic jargon, and conventional generalizations, the book is meant to provide graduates and managers with a framework for negotiating and influencing across cultures.</p>
        <p>The goal is to overcome Western (particularly US) ethnocentrism, moving out of laboratory simulations and providing a model based on real life exposure to international negotiations and managerial challenges.</p>
      </div>
      <p class="bio"><span class="author-name">Darvesh K. Molan</span> is Professor of Cultural Management at the Aurelian University in Milan, Italy, and founder of Tradvia, a management consultancy firm that assists companies in international negotiations and global teams performance improvement. He has previously lived and worked in eight countries and four different continents, leading cross functional teams implementing post M&amp;A integration strategies and managing commercial and marketing organizations in Europe, North &amp; South America, Middle East and South &amp; East Asia.</p>
    </section>

    <section class="spine">
      <svg width="60" height="744" viewBox="0 0 60 744">
        <g font-family="Arimo, Arial, sans-serif" font-weight="700">
          <text transform="translate(22 78) rotate(90)" fill="var(--orange)" font-size="21">The Bridge Method</text>
          <text transform="translate(34 320) rotate(90)" fill="var(--orange)" font-size="13">Practical Dialogue and Persuasion</text>
          <text transform="translate(17 320) rotate(90)" fill="var(--orange)" font-size="13">Methods for Cross-Border Success</text>
          <text transform="translate(22 564) rotate(90)" fill="var(--white)" font-size="16">Darvesh K. Molan</text>
        </g>
      </svg>
    </section>

    <section class="front">
      <div class="tab tab-left"></div>
      <div class="tab tab-right"></div>
      <h1 class="title">The Bridge Method</h1>
      <h2 class="subtitle">Practical Dialogue and Persuasion<br>Methods for Cross-Border Success</h2>
      <div class="emblem-area" role="img" aria-label="Cover artwork: a world globe over overlapping coloured blocks"></div>
      <p class="author">Darvesh K. Molan</p>
    </section>
  </div>
</body>
</html>
```